Printer Cartridges Supplier Namecard

Attached is my company logo and the design of my current namecard. I would like to have a more special look for it. Can have a little cuteness too rather than those normal standard feel. I'm a supplier mainly dealing with original and compatible printer toner cartridges, some other products like paper supplies as well.

Target Market(s)

Companies, businesses, corporates

Industry/Entity Type

It Company

Contact Information for Business Card

Logo, name, contact, address, supplies and maybe a slogan

Colors
85cae6
33a6d7
3176b5
0255a3
0792cd
85abd2

Requirements
Must have
• Logo, name, contact and address basic details.
• Must include some pictures, not just rearrange what I'm currently having.
Nice to have
• Be creative and bold, a diiferent traditional feel.

```html
<!DOCTYPE html>
<html lang="en">
<head>
<meta charset="UTF-8">
<title>Cartwell Namecard</title>
<link href="https://fonts.googleapis.com/css2?family=Roboto:wght@300;400;500&family=Roboto+Condensed:wght@700&display=swap" rel="stylesheet">
<style>
  :root {
    --backdrop: #2a2a2a;
    --card-white: #f3f3f3;
    --sky: #62b4e4;
    --slate: #58595b;
    --ink-grey: #5a5a5a;
    --white: #ffffff;
  }
  * { margin: 0; padding: 0; box-sizing: border-box; }
  html, body {
    width: 1200px; height: 960px; overflow: hidden;
    background: var(--backdrop);
    font-family: "Roboto", Arial, sans-serif;
  }
  .stage { position: relative; width: 1200px; height: 960px; }
  .card {
    position: absolute; width: 600px; height: 342px; overflow: hidden;
  }
  .card-front { left: 302px; top: 129px; background: var(--card-white); }
  .card-back { left: 299px; top: 489px; background: var(--slate); color: var(--white); }

  .front-bands { position: absolute; inset: 0; }

  .holder { position: absolute; left: 26px; top: 22px; color: var(--white); }
  .holder-name {
    font-family: "Roboto Condensed", "Arial Narrow", sans-serif;
    font-weight: 700; font-size: 21px; letter-spacing: 0.2px; line-height: 1;
  }
  .holder-role { font-weight: 500; font-size: 15px; margin-top: 5px; }

  .contact { position: absolute; left: 26px; top: 138px; color: var(--white); font-size: 14.5px; line-height: 18px; font-weight: 400; }
  .contact-lines { margin-top: 10px; }
  .contact-item { display: flex; align-items: center; gap: 6px; }
  .contact-item svg { width: 13px; height: 13px; fill: var(--white); }

  .website {
    position: absolute; left: 26px; top: 310px; color: var(--white);
    font-size: 15px; font-weight: 500; letter-spacing: 4.2px;
  }

  .brand-front { position: absolute; left: 370px; top: 166px; width: 205px; color: var(--ink-grey); }
  .brand-name { font-weight: 300; font-size: 40px; line-height: 1; letter-spacing: -0.5px; white-space: nowrap; }
  .brand-tagline { font-size: 9.5px; font-weight: 400; margin-top: 5px; white-space: nowrap; }

  .brand-back {
    position: absolute; left: 0; right: 0; top: 120px;
    display: flex; align-items: center; justify-content: center; gap: 14px;
  }
  .brand-mark { width: 56px; height: 56px; background: var(--white); border-radius: 8px; }
  .brand-back .brand-name { font-size: 52px; color: var(--white); }
  .brand-back .brand-tagline { color: var(--white); font-size: 10px; }

  .services {
    position: absolute; left: 0; right: 0; top: 271px; text-align: center;
    font-size: 15px; line-height: 18px;
  }
  .services .dot { display: inline-block; width: 5px; height: 5px; border-radius: 50%; background: var(--white); vertical-align: middle; margin: 0 3px; }
</style>
</head>
<body>
<main class="stage">

  <section class="card card-front">
    <svg class="front-bands" width="600" height="342" viewBox="0 0 600 342" aria-hidden="true">
      <path d="M0 0 H202 Q224 0 224 22 V85 H0 Z" fill="var(--sky)"/>
      <path d="M0 108 H300 Q340 108 340 148 V290 Q340 330 300 330 H0 Z" fill="var(--sky)"/>
      <path d="M0 268 H233 Q255 268 255 290 V342 H0 Z" fill="var(--card-white)"/>
      <rect x="0" y="292" width="228" height="50" fill="var(--sky)"/>
    </svg>

    <div class="holder">
      <div class="holder-name">MIRA TAN</div>
      <div class="holder-role">Sales Executive</div>
    </div>

    <div class="contact">
      <div>412A Harbourlight Avenue</div>
      <div>#05-118</div>
      <div>Singapore 530412</div>
      <div class="contact-lines">
        <div class="contact-item">
          <svg viewBox="0 0 24 24"><path d="M6.6 10.8a15.2 15.2 0 0 0 6.6 6.6l2.2-2.2c.3-.3.7-.4 1-.2 1.1.4 2.3.6 3.6.6.6 0 1 .4 1 1V20c0 .6-.4 1-1 1C10.6 21 3 13.4 3 4c0-.6.4-1 1-1h3.5c.6 0 1 .4 1 1 0 1.3.2 2.5.6 3.6.1.3 0 .7-.2 1z"/></svg>
          <span>HP 9000 1234</span>
        </div>
        <div class="contact-item">
          <svg viewBox="0 0 24 24"><path d="M2 5h20v14H2z M2 5l10 8 10-8" fill="none" stroke="#fff" stroke-width="2"/></svg>
          <span>mira@cartwell.sg</span>
        </div>
      </div>
    </div>

    <div class="website">www.cartwell.sg</div>

    <div class="brand-front">
      <div class="brand-name">cartwell.sg</div>
      <div class="brand-tagline">Compatible printer ink and toner solutions</div>
    </div>
  </section>

  <section class="card card-back">
    <div class="brand-back">
      <span class="brand-mark"></span>
      <div>
        <div class="brand-name">cartwell.sg</div>
        <div class="brand-tagline">Compatible printer ink and toner solutions</div>
      </div>
    </div>
    <div class="services">
      <div>Printer Ink &amp; Toner Cartridges<span class="dot"></span>Original Printer Cartridges</div>
      <div>Paper Products<span class="dot"></span>Printer Maintainence &amp; Repair</div>
    </div>
  </section>

</main>
</body>
</html>
```